TavenLaw a fully remote and fully bilingual law firm for the Florida injured

1. Can you describe what your company does?- a solo lawyer practice in Florida, D.C., and soon in NY. I offer services for auto accidents, negligence, boat accident, motorcycle accident, insurance claims, premises liability, and things of the like.

2. Who are your target customers for the website? Drivers, passengers, pedestrians involved in accidents where they were injured and need help making a claim against the other vehicle or insurance company- throughout the entire state of Florida, but primarily in greater central florida area for english speaking and latino community offering a 100% bilingual services ENGLISH/SPANISH and 100% remote, where I wont make clients come to an office ever, and will private online meetings, signing portals, and all to have it efficient for clients benefit.

3. Do you have an existing domain name / website address? yes, tavenlaw.com through zentrova workspace. i need help in getting in brought to you so you can handle it please.

4. In addition to a Home Page, which other pages / sections would you like your website to have:
About Us
Contact Us
Products / Services
Office / Mailing Address
Testimonials / Reviews
FAQs
Terms and Conditions
Any other page / section you would like- DO EVERYTHING IN BOTH LANGUAGES- ENGLISH AND SPANISH
I want the page to have a way for people to calendar appts with me. and also
to make transactions - accepting all methods of payment

For each of the pages / sections you’d like to have, please provide the text (and images, if available) you would like to include.

5. Which of the below are features and functionalities your website will need:
Image Gallery
Videos
Contact Form
Mailing List
Maps
FAQs
Accepting payments / donations
6. Please provide the URLs for the social media profiles you'd like to link to the website. I have none, I am just starting, I actually want to have the online presence ready before my official launch.

Injured individuals by the negligent act of another in Florida

LAWYER/ AUTO ACCIDENT/NEGLIGENCE/ PREMISES LIABILITY/ CIVIL LAW

Coded - Design and coding required

1 page

• bilingual ENGLISH and SPANISH; a button for people to calendar appointments with me; accept payments, and to be able to integrate with major software like docusign, adobe, etc since I need to integrate under the fully remote platform
• look at my logo from artkiln.com it has the Tavenbrook Law and TavenLaw.com together.. I have the tavenlaw.com domain from zentrova. need you guys to help integrate that too , meaning to be able to use that domain for my website.

```html
<!DOCTYPE html>
<html lang="en">
<head>
<meta charset="utf-8">
<title>Services | Tavenbrook Law</title>
<link rel="stylesheet" href="https://fonts.googleapis.com/css2?family=Poppins:wght@400;500;600&family=Bebas+Neue&family=Cinzel:wght@400;500&display=swap">
<style>
:root{
  --navy:#1b2f5e;
  --navy-deep:#14234a;
  --gold:#d4a33b;
  --text:#555a63;
  --light:#f4f4f4;
  --white:#ffffff;
  --black:#050505;
  --footer-text:#e6e6e6;
}
*{box-sizing:border-box;margin:0;padding:0}
html,body{width:1200px;height:3555px;overflow:hidden}
body{font-family:'Poppins',sans-serif;color:var(--text);background:var(--white);position:relative}

/* Header / hero */
.hero{position:absolute;left:0;top:0;width:1200px;height:520px;overflow:hidden}
.hero-photo{position:absolute;inset:0;background:linear-gradient(100deg,#1c2c5a 0%,#2a3a66 40%,#55576a 65%,#6b5a4c 85%,#3a2b22 100%)}
.hero-shade{position:absolute;inset:0;background:linear-gradient(90deg,rgba(20,35,74,.85) 0%,rgba(20,35,74,.55) 45%,rgba(20,35,74,.1) 100%)}
.brand{position:absolute;left:22px;top:14px;width:176px;display:flex;flex-direction:column;align-items:center;gap:10px}
.brand-mark{width:58px;height:58px;border-radius:50%;border:2px solid var(--white)}
.brand-name{font-family:'Poppins',sans-serif;font-weight:500;color:var(--white);font-size:14px;letter-spacing:3px;white-space:nowrap}
.nav{position:absolute;left:218px;top:32px;display:flex;gap:18px;font-size:12.5px;color:var(--white);white-space:nowrap}
.nav .active{color:var(--gold)}
.lang{position:absolute;left:740px;top:26px;width:82px;height:30px;border:1px solid var(--white);border-radius:15px;display:flex;align-items:center;justify-content:center;gap:6px;color:var(--white);font-size:12px}
.lang-dot{width:16px;height:16px;border-radius:50%;background:#c9d3ea}
.divider-v{position:absolute;left:836px;top:22px;height:38px;border-left:1px dashed rgba(255,255,255,.6)}
.pay-btn{position:absolute;left:852px;top:22px;width:151px;height:38px;border-radius:19px;background:var(--gold);color:var(--white);font-size:13px;display:flex;align-items:center;justify-content:center}
.call{position:absolute;left:1015px;top:21px;display:flex;align-items:center;gap:10px;color:var(--white)}
.call-icon{width:34px;height:34px;border-radius:50%;background:var(--gold);display:flex;align-items:center;justify-content:center}
.call small{display:block;font-size:12px}
.call strong{display:block;font-size:16.5px;font-weight:600;white-space:nowrap}
.hero-title{position:absolute;left:142px;top:168px;border-left:3px solid var(--gold);padding-left:14px;font-family:'Cinzel',serif;color:var(--white);font-size:41px;line-height:52px}
.hero-text{position:absolute;left:142px;top:238px;width:370px;color:var(--white);font-size:12.5px;line-height:22.5px}
.hero-cta{position:absolute;left:142px;top:349px;width:254px;height:43px;border-radius:22px;background:var(--gold);color:var(--white);font-size:13px;display:flex;align-items:center;justify-content:center;gap:12px}
.hero-curve{position:absolute;left:0;top:430px}
.breadcrumb-band{position:absolute;left:0;top:520px;width:1200px;height:37px;background:var(--light)}
.breadcrumb{position:absolute;left:141px;top:527px;font-size:13px;color:#8891a6}
.breadcrumb span{color:var(--navy)}

/* Services */
.section-title{position:absolute;left:0;top:636px;width:1200px;text-align:center;font-family:'Bebas Neue',sans-serif;font-size:42px;color:var(--navy);letter-spacing:2px}
.gold-rule{height:2px;width:50px;background:var(--gold)}
.section-title + .gold-rule{position:absolute;left:575px;top:690px}
.section-intro{position:absolute;left:262px;top:712px;width:676px;text-align:center;font-size:14px;line-height:26px;color:#444}
.service{position:absolute;left:163px;width:873px;height:300px}
.service-text{position:absolute;top:0;width:437px}
.service.right .service-text{left:0}
.service.left .service-text{left:437px}
.service-icon{width:48px;height:44px;display:block}
.service h3{margin-top:17px;font-size:19px;font-weight:500;color:var(--navy)}
.service .gold-rule{margin-top:10px}
.service p{font-size:12.5px;line-height:22.5px;margin-top:20px;text-align:justify}
.service p + p{margin-top:14px}
.service-photo{position:absolute;top:0;width:385px;height:266px}
.service.right .service-photo{left:489px}
.service.left .service-photo{left:0}
.service-photo::before{content:"";position:absolute;top:9px;width:385px;height:266px;border:1.5px solid var(--navy);z-index:0}
.service.right .service-photo::before{left:9px}
.service.left .service-photo::before{left:-9px}
.photo-fill{position:relative;z-index:1;width:100%;height:100%}
.closing{position:absolute;left:163px;top:2853px;width:897px;font-size:12.5px;line-height:22.5px}
.closing p + p{margin-top:14px}

/* Footer */
.footer{position:absolute;left:0;top:3088px;width:1200px;height:467px;background:var(--black);overflow:hidden}
.footer-curve{position:absolute;left:0;top:0}
.footer-ring{position:absolute;left:752px;top:112px;width:380px;height:380px;border-radius:50%;border:26px solid rgba(255,255,255,.04)}
.footer-brand{position:absolute;left:66px;top:176px;width:240px;display:flex;flex-direction:column;align-items:center;gap:14px}
.footer-brand .brand-mark{width:78px;height:78px;border-width:3px}
.footer-brand .brand-name{font-size:19px;letter-spacing:4px}
.socials{position:absolute;left:110px;top:318px;display:flex;gap:9px}
.social{width:32px;height:32px;border-radius:50%;border:1.5px solid var(--white);color:var(--white);font-size:7.5px;display:flex;align-items:center;justify-content:center}
.social.primary{background:#2d4f9c;border-color:#2d4f9c}
.footer-col{position:absolute;top:152px}
.footer-col h4{font-family:'Bebas Neue',sans-serif;font-weight:400;font-size:21px;letter-spacing:1.5px;color:var(--white)}
.footer-col .gold-rule{width:34px;margin-top:6px;margin-bottom:18px}
.footer-col li{list-style:none;font-size:12.5px;color:var(--footer-text);line-height:27.6px;white-space:nowrap}
.contact li{display:flex;gap:12px;line-height:19px;margin-bottom:15px}
.contact svg{flex:none;margin-top:2px}
.footer-rule{position:absolute;left:70px;top:398px;width:1060px;height:1px;background:rgba(255,255,255,.2)}
.copyright{position:absolute;left:70px;top:422px;font-size:12.5px;color:var(--footer-text)}
.copyright b{font-weight:500;color:var(--white)}
.cards{position:absolute;left:903px;top:416px;display:flex;gap:5px}
.card{width:41px;height:28px;border-radius:3px;background:var(--white);color:var(--navy);font-size:8.5px;font-weight:600;display:flex;align-items:center;justify-content:center}
</style>
</head>
<body>

<header class="hero">
  <div class="hero-photo" role="img" aria-label="Photo of a lawyer reading a book beside a wooden gavel and scales of justice"></div>
  <div class="hero-shade"></div>
  <div class="brand"><span class="brand-mark"></span><span class="brand-name">TAVENBROOK LAW</span></div>
  <nav class="nav">
    <span>Home</span><span>About Us</span><span class="active">Services</span><span>Testimonials</span><span>FAQ's</span><span>Blog</span><span>Contact Us</span>
  </nav>
  <div class="lang"><span class="lang-dot"></span>EN
    <svg width="8" height="6" viewBox="0 0 8 6"><path d="M1 1l3 3 3-3" stroke="#fff" fill="none" stroke-width="1.3"/></svg>
  </div>
  <div class="divider-v"></div>
  <div class="pay-btn">Make a Payment</div>
  <div class="call">
    <span class="call-icon"><svg width="16" height="16" viewBox="0 0 24 24"><path fill="#fff" d="M6.6 10.8a15.1 15.1 0 006.6 6.6l2.2-2.2a1 1 0 011-.25 11.4 11.4 0 003.6.57 1 1 0 011 1V20a1 1 0 01-1 1A17 17 0 013 4a1 1 0 011-1h3.5a1 1 0 011 1c0 1.25.2 2.45.57 3.57a1 1 0 01-.25 1z"/></svg></span>
    <span><small>Call Us Today</small><strong>407 555 0139</strong></span>
  </div>
  <h1 class="hero-title">Services</h1>
  <p class="hero-text">Bilingual legal services for auto accidents, negligence claims, and personal injury cases throughout Florida, DC, and soon NY. 100% remote consultations available.</p>
  <div class="hero-cta">Schedule Free Consultation
    <svg width="24" height="12" viewBox="0 0 24 12"><path d="M0 6h22M17 1l5 5-5 5" stroke="#fff" fill="none" stroke-width="1.6"/></svg>
  </div>
  <svg class="hero-curve" width="1200" height="90" viewBox="0 0 1200 90">
    <path d="M0 18 Q600 140 1200 18 L1200 90 L0 90Z" fill="#f4f4f4"/>
    <path d="M0 12 Q600 134 1200 12" stroke="#d4a33b" stroke-width="3" fill="none"/>
    <circle cx="598" cy="75" r="20" fill="#fff" stroke="#e3e3e3"/>
    <path d="M589 71l9 8 9-8" stroke="#1b2f5e" stroke-width="2" fill="none"/>
  </svg>
</header>
<div class="breadcrumb-band"></div>
<div class="breadcrumb">Home &nbsp;»&nbsp; <span>Services</span></div>

<main>
  <h2 class="section-title">SERVICES</h2>
  <div class="gold-rule"></div>
  <p class="section-intro">I offer services for auto accidents, negligence, boat accident, motorcycle accident, insurance claims, premises liability, and things of the like.</p>

  <section class="service right" style="top:796px">
    <div class="service-text">
      <svg class="service-icon" viewBox="0 0 48 44" fill="none" stroke="#1b2f5e" stroke-width="1.6"><rect x="3" y="22" width="32" height="12" rx="3"/><path d="M8 22l4-8h14l4 8"/><circle cx="10" cy="36" r="3"/><circle cx="28" cy="36" r="3"/><path d="M38 4l2 6 5-3-3 5 5 2-6 1"/></svg>
      <h3>Auto Accident</h3><div class="gold-rule"></div>
      <p>Duis autem vel eum iriure dolor inm hendrerit in vulputate. On the other hand, we denounce with righteous indignation and dislike men who are so beguiled and demoralized by the charms.</p>
      <p>But I must explain to you how all this mistaken idea of denouncing pleasure and praising pain was born and I will give you a complete account of the system.</p>
    </div>
    <div class="service-photo"><div class="photo-fill" role="img" aria-label="Photo of two cars crashed together on a road" style="background:linear-gradient(135deg,#3d4a3a,#6e7478 50%,#8a8c8e)"></div></div>
  </section>

  <section class="service left" style="top:1147px">
    <div class="service-photo"><div class="photo-fill" role="img" aria-label="Photo of a distressed client meeting with a lawyer over documents" style="background:linear-gradient(135deg,#6b6a66,#9a8f82 50%,#c8c2b8)"></div></div>
    <div class="service-text">
      <svg class="service-icon" viewBox="0 0 48 44" fill="none" stroke="#1b2f5e" stroke-width="1.6"><circle cx="20" cy="7" r="4"/><path d="M20 12v14l-6 14M20 26l6 14M12 18h16"/><circle cx="34" cy="32" r="7"/><path d="M31 29l6 6M37 29l-6 6"/></svg>
      <h3>Negligence</h3><div class="gold-rule"></div>
      <p>Duis autem vel eum iriure dolor inm hendrerit in vulputate. On the other hand, we denounce with righteous indignation and dislike men who are so beguiled and demoralized by the charms.</p>
      <p>But I must explain to you how all this mistaken idea of denouncing pleasure and praising pain was born and I will give you a complete account of the system.</p>
    </div>
  </section>

  <section class="service right" style="top:1499px">
    <div class="service-text">
      <svg class="service-icon" viewBox="0 0 48 44" fill="none" stroke="#1b2f5e" stroke-width="1.6"><path d="M4 30h32l-4 8H8z"/><rect x="10" y="18" width="18" height="12"/><path d="M16 18V8l8 4-8 4M2 42c4-3 8-3 12 0s8 3 12 0 8-3 12 0"/></svg>
      <h3>Boat Accident</h3><div class="gold-rule"></div>
      <p>Duis autem vel eum iriure dolor inm hendrerit in vulputate. On the other hand, we denounce with righteous indignation and dislike men who are so beguiled and demoralized by the charms.</p>
      <p>But I must explain to you how all this mistaken idea of denouncing pleasure and praising pain was born and I will give you a complete account of the system.</p>
    </div>
    <div class="service-photo"><div class="photo-fill" role="img" aria-label="Photo of a small boat sinking in open water" style="background:linear-gradient(160deg,#5f7a86,#2f5162 60%,#1f3d4e)"></div></div>
  </section>

  <section class="service left" style="top:1851px">
    <div class="service-photo"><div class="photo-fill" role="img" aria-label="Photo of a fallen motorcycle on a road after a crash" style="background:linear-gradient(150deg,#5a6e3e,#8b8e8c 45%,#6a6d70)"></div></div>
    <div class="service-text">
      <svg class="service-icon" viewBox="0 0 48 44" fill="none" stroke="#1b2f5e" stroke-width="1.6"><circle cx="8" cy="34" r="5"/><circle cx="32" cy="34" r="5"/><path d="M8 34l10-10h10l4 10M28 24l6-10"/><circle cx="36" cy="8" r="3"/></svg>
      <h3>Motorcycle Accident</h3><div class="gold-rule"></div>
      <p>Duis autem vel eum iriure dolor inm hendrerit in vulputate. On the other hand, we denounce with righteous indignation and dislike men who are so beguiled and demoralized by the charms.</p>
      <p>But I must explain to you how all this mistaken idea of denouncing pleasure and praising pain was born and I will give you a complete account of the system.</p>
    </div>
  </section>

  <section class="service right" style="top:2202px">
    <div class="service-text">
      <svg class="service-icon" viewBox="0 0 48 44" fill="none" stroke="#1b2f5e" stroke-width="1.6"><rect x="6" y="2" width="26" height="36" rx="2"/><path d="M12 12h14M12 18h14M12 24h8"/><circle cx="19" cy="30" r="3"/><path d="M30 38l12-14 3 3-12 14h-3z"/></svg>
      <h3>Insurance Claims</h3><div class="gold-rule"></div>
      <p>Duis autem vel eum iriure dolor inm hendrerit in vulputate. On the other hand, we denounce with righteous indignation and dislike men who are so beguiled and demoralized by the charms.</p>
      <p>But I must explain to you how all this mistaken idea of denouncing pleasure and praising pain was born and I will give you a complete account of the system.</p>
    </div>
    <div class="service-photo"><div class="photo-fill" role="img" aria-label="Photo of hands holding an insurance policy document on a desk" style="background:linear-gradient(135deg,#8a6a4a,#d8d4cc 45%,#a88a6c)"></div></div>
  </section>

  <section class="service left" style="top:2554px">
    <div class="service-photo"><div class="photo-fill" role="img" aria-label="Photo of a judge's gavel and building models on a desk with a person signing papers" style="background:linear-gradient(120deg,#5b8ec0,#8fa78a 45%,#8a5a3a)"></div></div>
    <div class="service-text">
      <svg class="service-icon" viewBox="0 0 48 44" fill="none" stroke="#1b2f5e" stroke-width="1.6"><circle cx="30" cy="12" r="8"/><path d="M27 12l2 2 4-4"/><circle cx="10" cy="8" r="3"/><path d="M10 12l2 12-6 14M12 24l8 14M4 16l8 2 10-2"/></svg>
      <h3>Premises Liability</h3><div class="gold-rule"></div>
      <p>Duis autem vel eum iriure dolor inm hendrerit in vulputate. On the other hand, we denounce with righteous indignation and dislike men who are so beguiled and demoralized by the charms.</p>
      <p>But I must explain to you how all this mistaken idea of denouncing pleasure and praising pain was born and I will give you a complete account of the system Nam libero tempore nobis est.</p>
    </div>
  </section>

  <div class="closing">
    <p>At vero eos et accusamus et iusto odio dignissimos ducimus qui blanditiis praesentium voluptatum deleniti atque corrupti quos dolores et quas molestias excepturi sint occaecati cupiditate non provident, similique sunt in culpa qui officia deserunt mollitia animi, id est laborum et dolorum fuga. Et harum quidem rerum facilis est et expedita distinctio. Nam libero tempore</p>
    <p>Cum soluta nobis est eligendi optio cumque nihil impedit quo minus id quod maxime placeat facere possimus, omnis voluptas assumenda est, omnis dolor repellendus. Temporibus autem quibusdam et aut officiis debitis aut rerum necessitatibus saepe eveniet ut et voluptates repudiandae sint et molestiae non recusandae. Itaque earum rerum hic tenetur a sapiente delectus, ut aut reiciendis voluptatibus maiores alias consequatur aut perferendis doloribus asperiores repellat.</p>
  </div>
</main>

<footer class="footer">
  <div class="footer-ring"></div>
  <svg class="footer-curve" width="1200" height="80" viewBox="0 0 1200 80">
    <path d="M0 0 H1200 V10 Q600 120 0 10Z" fill="#fff"/>
    <path d="M0 16 Q600 126 1200 16" stroke="#d4a33b" stroke-width="3" fill="none"/>
  </svg>
  <div class="footer-brand"><span class="brand-mark"></span><span class="brand-name">TAVENBROOK LAW</span></div>
  <div class="socials">
    <span class="social primary">Nexo</span><span class="social">Vyne</span><span class="social">Orbi</span><span class="social">Pixa</span>
  </div>
  <div class="footer-col" style="left:414px">
    <h4>QUICK LINKS</h4><div class="gold-rule"></div>
    <ul><li>Home</li><li>About Us</li><li>Services</li><li>Testimonials</li><li>FAQ's</li><li>Contact Us</li><li>Make a Payment</li></ul>
  </div>
  <div class="footer-col" style="left:625px">
    <h4>SERVICES</h4><div class="gold-rule"></div>
    <ul><li>Auto Accident</li><li>Negligence</li><li>Motorcycle Accident</li><li>Motorcycle Accident</li><li>Insurance Claims</li><li>Motorcycle Accident</li></ul>
  </div>
  <div class="footer-col contact" style="left:872px">
    <h4>CONTACT DETAILS</h4><div class="gold-rule"></div>
    <ul>
      <li><svg width="12" height="16" viewBox="0 0 12 16"><path fill="#d4a33b" d="M6 0a6 6 0 00-6 6c0 4.5 6 10 6 10s6-5.5 6-10a6 6 0 00-6-6zm0 8.5A2.5 2.5 0 116 3.5a2.5 2.5 0 010 5z"/></svg><span>48, Lakeview Court Road,<br>Orlando. FL - 328 01</span></li>
      <li><svg width="14" height="14" viewBox="0 0 24 24"><path fill="#d4a33b" d="M6.6 10.8a15.1 15.1 0 006.6 6.6l2.2-2.2a1 1 0 011-.25 11.4 11.4 0 003.6.57 1 1 0 011 1V20a1 1 0 01-1 1A17 17 0 013 4a1 1 0 011-1h3.5a1 1 0 011 1c0 1.25.2 2.45.57 3.57a1 1 0 01-.25 1z"/></svg><span>(407) 555-0182</span></li>
      <li><svg width="14" height="12" viewBox="0 0 14 12"><rect width="14" height="12" rx="1.5" fill="#d4a33b"/><path d="M1 2l6 4.5L13 2" stroke="#000" stroke-width="1.2" fill="none"/></svg><span>info@tavenlaw.com</span></li>
      <li><svg width="14" height="14" viewBox="0 0 14 14"><circle cx="7" cy="7" r="6" stroke="#d4a33b" stroke-width="1.6" fill="none"/><path d="M7 3.5V7l2.5 1.5" stroke="#d4a33b" stroke-width="1.4" fill="none"/></svg><span>Monday - Friday: 9:00 AM - 6:00 PM<br>Weekends: By appointment only</span></li>
    </ul>
  </div>
  <div class="footer-rule"></div>
  <p class="copyright">© 2025 Tavenbrook Law. All rights reserved. &nbsp;| &nbsp;<b>Terms and Conditions</b></p>
  <div class="cards">
    <span class="card">Carda</span><span class="card">Finvo</span><span class="card">Paxel</span><span class="card">Quidly</span><span class="card">Strata</span>
  </div>
</footer>

</body>
</html>
```